Business Card Design Project

Business Card
We are rebranding with a new logo
Industry/Entity Type
Business
Contact Information for Business Card
Dennis Morvale +61 487215963 dennis@quorv.com.au P.O. Box 872 Fernlow QLD 4309
Requirements
Must have
- Logo

```html
<!DOCTYPE html>
<html lang="en">
<head>
<meta charset="UTF-8">
<title>Quorv International – Business Card</title>
<link rel="stylesheet" href="https://fonts.googleapis.com/css2?family=Lato:wght@300;400;700&display=swap">
<style>
  :root {
    --stage: #e6e8eb;
    --card-white: #ffffff;
    --blue-deep: #173a5e;
    --blue-mid: #0f5d93;
    --blue-bright: #0a8fd4;
    --brand-blue: #1479b8;
    --accent-orange: #f08a1c;
    --text-light: #ffffff;
  }
  html, body {
    margin: 0;
    padding: 0;
    width: 1200px;
    height: 926px;
    overflow: hidden;
    background: var(--stage);
    font-family: "Lato", sans-serif;
  }
  .canvas {
    position: relative;
    width: 1200px;
    height: 926px;
  }
  .business-card {
    position: absolute;
    left: 150px;
    top: 190px;
    width: 900px;
    height: 546px;
    background: var(--card-white);
    box-shadow: 0 10px 30px rgba(0,0,0,0.18);
    overflow: hidden;
  }
  .card-panel {
    position: absolute;
    inset: 0;
  }
  .brand {
    position: absolute;
    left: 62px;
    top: 218px;
    display: flex;
    align-items: center;
    gap: 14px;
  }
  .brand-dot {
    width: 18px;
    height: 18px;
    border-radius: 50%;
    background: var(--accent-orange);
    flex: none;
  }
  .brand-name {
    color: var(--brand-blue);
    font-weight: 700;
    font-size: 30px;
    line-height: 1.1;
    letter-spacing: 1px;
  }
  .contact {
    position: absolute;
    left: 500px;
    top: 205px;
    color: var(--text-light);
  }
  .contact-name {
    margin: 0;
    font-size: 38px;
    font-weight: 300;
    letter-spacing: 0.5px;
  }
  .contact-name strong { font-weight: 700; }
  .rule {
    width: 30px;
    height: 3px;
    background: var(--accent-orange);
    margin: 14px 0 8px;
  }
  .contact-line {
    margin: 0;
    font-size: 25px;
    font-weight: 300;
    line-height: 1.32;
  }
  .contact-label {
    color: var(--accent-orange);
    font-weight: 700;
    margin-right: 6px;
  }
  .contact-address {
    margin: 14px 0 0;
    font-size: 27px;
    font-weight: 300;
  }
</style>
</head>
<body>
<div class="canvas">
  <div class="business-card">
    <svg class="card-panel" width="900" height="546" viewBox="0 0 900 546" aria-hidden="true">
      <defs>
        <linearGradient id="panelGradient" x1="0" y1="1" x2="1" y2="0">
          <stop offset="0" stop-color="var(--blue-deep)"/>
          <stop offset="0.55" stop-color="var(--blue-mid)"/>
          <stop offset="1" stop-color="var(--blue-bright)"/>
        </linearGradient>
      </defs>
      <polygon points="442,0 900,0 900,546 182,546" fill="url(#panelGradient)"/>
    </svg>

    <div class="brand">
      <span class="brand-dot"></span>
      <span class="brand-name">Quorv<br>International</span>
    </div>

    <div class="contact">
      <h1 class="contact-name">DENNIS <strong>MORVALE</strong></h1>
      <div class="rule"></div>
      <p class="contact-line"><span class="contact-label">T.</span>+61 487215963</p>
      <p class="contact-line"><span class="contact-label">E.</span>dennis@quorv.com.au</p>
      <div class="rule"></div>
      <p class="contact-address">P.O. Box 872 Fernlow QLD 4309</p>
    </div>
  </div>
</div>
</body>
</html>
```